Business Card for premium dental clinic

We are a premium dental clinic based in Brasov, Romania with more than 15 year on the market, providing quality dental treatment made by a team of more specialized dentists, working with modern equipment as a solution to beautiful and healthy teeth.

Our current logo for the clinic use 2 square with colors black and gold - dr Ternisu - studio, using family fonts Bodoni, Myriad Pro and Segoe Print.
Depending on the printing we used some gold CMYK background or gold foil picture background or a gold gradient.
We want a business card:
- eye catching business card
- distinguished business card
- premium design
- to keep the color scheme of black and gold
- to attract the customers to spent time reading the information
- modern concept

```html
<!DOCTYPE html>
<html lang="en">
<head>
<meta charset="utf-8">
<title>Aurora Dental Clinic – Business Card</title>
<link rel="stylesheet" href="https://fonts.googleapis.com/css2?family=Oswald:wght@300;400&family=Roboto:wght@400&display=swap">
<style>
  :root {
    --bg: #4a4a4a;
    --card: #262626;
    --gold-light: #f7d23a;
    --gold: #e2b21c;
    --gold-deep: #b8860b;
    --white: #ffffff;
    --ink: #1a1a1a;
  }
  * { box-sizing: border-box; margin: 0; padding: 0; }
  html, body { width: 799px; height: 1200px; overflow: hidden; }
  body {
    background: var(--bg);
    position: relative;
    font-family: "Roboto", Arial, sans-serif;
  }
  .card {
    position: absolute;
    left: 60px;
    width: 679px;
    height: 388px;
    background: var(--card);
    box-shadow: 0 10px 30px rgba(0,0,0,.45);
    overflow: hidden;
  }
  .card--front { top: 150px; }
  .card--back { top: 662px; }

  .foil {
    background: linear-gradient(135deg, var(--gold-light) 0%, var(--gold) 45%, var(--gold-deep) 70%, var(--gold-light) 100%);
  }

  /* front */
  .front__foil {
    position: absolute; left: 0; top: 0;
    width: 335px; height: 100%;
  }
  .name-plate {
    position: absolute;
    left: 40px; top: 110px;
    width: 295px; height: 108px;
    background: var(--white);
    display: flex; align-items: center; justify-content: center;
  }
  .doctor-name {
    font-family: "Oswald", sans-serif;
    font-weight: 300;
    color: var(--ink);
    line-height: 1;
    letter-spacing: -1px;
    white-space: nowrap;
  }
  .doctor-name__title { font-size: 34px; }
  .doctor-name__surname { font-size: 60px; }

  /* clinic name */
  .brand {
    position: absolute;
    display: flex;
    align-items: flex-start;
    gap: 14px;
    color: var(--white);
  }
  .brand__dot {
    width: 14px; height: 14px; border-radius: 50%;
    background: var(--gold);
    margin-top: 22px;
    flex: none;
  }
  .brand__name {
    font-family: "Oswald", sans-serif;
    font-weight: 400;
    font-size: 46px;
    line-height: 1.15;
    white-space: nowrap;
  }
  .card--front .brand { left: 380px; top: 130px; }

  /* back */
  .card--back .brand { left: 60px; top: 110px; }
  .back__plate {
    position: absolute;
    left: 420px; top: 150px;
    width: 220px; height: 76px;
    display: flex; align-items: center; justify-content: center;
  }
  .back__plate .doctor-name__title { font-size: 24px; }
  .back__plate .doctor-name__surname { font-size: 46px; font-weight: 400; }

  .contact {
    position: absolute;
    left: 380px; top: 250px;
    list-style: none;
    color: var(--white);
    font-size: 15px;
    line-height: 23px;
  }
  .contact__item { display: flex; align-items: center; gap: 10px; }
  .contact__icon { width: 14px; height: 14px; flex: none; }
  .contact__address { margin-top: 2px; }
</style>
</head>
<body>

<section class="card card--front" aria-label="Business card front">
  <div class="front__foil foil" role="img" aria-label="Crumpled gold foil texture"></div>
  <div class="name-plate">
    <span class="doctor-name"><span class="doctor-name__title">dr.</span><span class="doctor-name__surname">ternisu</span></span>
  </div>
  <div class="brand">
    <span class="brand__dot"></span>
    <div class="brand__name">aurora<br>dental clinic</div>
  </div>
</section>

<section class="card card--back" aria-label="Business card back">
  <div class="brand">
    <span class="brand__dot"></span>
    <div class="brand__name">aurora<br>dental clinic</div>
  </div>
  <div class="back__plate foil" role="img" aria-label="Gold foil name plate">
    <span class="doctor-name"><span class="doctor-name__title">dr.</span><span class="doctor-name__surname">ternisu</span></span>
  </div>
  <ul class="contact">
    <li class="contact__item">
      <svg class="contact__icon" viewBox="0 0 24 24" aria-hidden="true"><path fill="#e2b21c" d="M6.6 10.8a15 15 0 0 0 6.6 6.6l2.2-2.2c.3-.3.7-.4 1-.2 1.1.4 2.3.6 3.6.6.6 0 1 .4 1 1V20c0 .6-.4 1-1 1A17 17 0 0 1 3 4c0-.6.4-1 1-1h3.5c.6 0 1 .4 1 1 0 1.3.2 2.5.6 3.6.1.3 0 .7-.2 1z"/></svg>
      268-410-2250
    </li>
    <li class="contact__item">
      <svg class="contact__icon" viewBox="0 0 24 24" aria-hidden="true"><rect x="2" y="5" width="20" height="14" fill="#e2b21c"/><path d="M2 5l10 8 10-8" fill="none" stroke="#262626" stroke-width="2"/></svg>
      office@aurora-dental.ro
    </li>
    <li class="contact__item">
      <svg class="contact__icon" viewBox="0 0 24 24" aria-hidden="true"><circle cx="12" cy="12" r="10" fill="#e2b21c"/><path d="M2 12h20M12 2c3 3 3 17 0 20M12 2c-3 3-3 17 0 20" fill="none" stroke="#262626" stroke-width="1.5"/></svg>
      www.aurora-dental.ro
    </li>
    <li class="contact__address">17 Livezii St., Brasov,<br>Brasov County, RO 500001</li>
  </ul>
</section>

</body>
</html>
```